Mental Health care Company in Washington DC

We are a new mental health care services provider in Washington DC. Please look at these sites.
https://brightwaterfamilysupport.com
https://www.quietharborinc.com
https://willowgate-dc.org/
https://www.tidepathdc.com
https://www.thelanternofdc.com

```html
<!DOCTYPE html>
<html lang="en">
<head>
<meta charset="utf-8">
<title>Calder Health Services</title>
<link href="https://fonts.googleapis.com/css2?family=Ubuntu:wght@400;500;700&family=Lato:wght@400;700&display=swap" rel="stylesheet">
<style>
:root{--navy:#0d2147;--orange:#f47c20;--teal:#8dcfd2;--teal-line:#8dcfd2;--grey:#f1f1f1;--text:#333;--muted:#666;}
*{box-sizing:border-box;margin:0;padding:0}
html,body{width:1200px;height:4265px;overflow:hidden}
body{font-family:"Lato",sans-serif;color:var(--text);background:#fff}
.page{position:relative;width:1200px;height:4265px;overflow:hidden}
.abs{position:absolute}
h1,h2,h3,.brand{font-family:"Ubuntu",sans-serif}
.accent{color:var(--orange)}
.topbar{top:0;left:0;width:1200px;height:33px;background:var(--navy);color:#fff;font-size:13px;display:flex;align-items:center;padding:0 112px;gap:40px}
.topbar .lang{margin-left:auto}
.nav{top:33px;left:0;width:1200px;height:86px;background:#fff;display:flex;align-items:center;padding:0 111px;border-bottom:1px solid #eee}
.brand{display:flex;flex-direction:column;color:var(--navy)}
.brand b{font-size:38px;font-weight:500;line-height:1}
.brand small{font-size:13px;letter-spacing:8px;color:var(--muted);text-align:center}
.menu{display:flex;gap:34px;margin-left:80px;font-size:14px;color:#222}
.menu .on{color:var(--orange);position:relative}
.menu .on:after{content:"";position:absolute;left:-4px;right:-4px;bottom:-30px;height:3px;background:var(--orange)}
.btn{background:var(--orange);color:#fff;font-weight:700;font-size:15px;border-radius:5px;display:inline-flex;align-items:center;justify-content:center}
.nav .search{margin-left:auto;margin-right:38px}
.hero{top:119px;left:0;width:1200px;height:609px;background:var(--grey)}
.hero .kicker{left:110px;top:92px;font-size:26px;color:#555}
.hero h1{left:110px;top:138px;font-size:41px;line-height:55px;color:var(--navy);font-weight:700}
.hero p{left:111px;top:254px;width:380px;font-size:13.5px;line-height:32px;color:#555}
.ph{background:linear-gradient(135deg,#c9b8a6,#8d7a6a)}
.section-head{text-align:center;width:1200px;left:0}
.section-head .eyebrow{font-size:15px;font-weight:700;color:var(--navy);letter-spacing:.5px}
.section-head h2{font-size:44px;font-weight:400;margin-top:10px;color:#111}
.section-head h2 span{font-weight:500;color:var(--orange)}
.section-head .rule{width:92px;height:3px;background:var(--teal-line);margin:18px auto 0}
.card{width:236px;height:438px;background:#fff;box-shadow:0 2px 10px rgba(0,0,0,.1);border-radius:6px;overflow:hidden}
.card .pic{height:218px}
.card.active{background:var(--teal);color:#fff}
.card.active .pic{border-radius:110px 110px 0 0}
.card .title{padding:18px 14px 0;font-family:"Ubuntu",sans-serif;font-size:21px;line-height:29px;position:relative}
.card .title span{color:var(--teal);font-weight:500}
.card.active .title{font-weight:500}
.card.active .title span{color:#fff}
.card .num{position:absolute;right:12px;top:16px;font-size:30px;color:#ccc;font-weight:300}
.card p{padding:8px 16px;font-size:12px;line-height:23px;color:#555}
.card.active p{color:#fff}
.card .more{position:absolute;left:16px;right:16px;bottom:14px;border-top:1px solid #ddd;padding-top:8px;font-size:12px;display:flex;justify-content:space-between;align-items:center}
.about{top:1503px;left:0;width:1200px;height:518px;background:var(--navy)}
.about-img{top:1495px;left:-4px;width:600px;height:526px;border-radius:0 263px 263px 0;border:4px solid #fff;border-left:0;background:linear-gradient(120deg,#c49a6c,#6b5447)}
.about .eyebrow{left:644px;top:55px;color:var(--orange);font-size:14px;font-weight:700}
.about h2{left:640px;top:78px;font-size:46px;font-weight:400;color:#fff}
.about .rule{left:641px;top:140px;width:90px;height:3px;background:var(--teal)}
.about p{left:640px;width:445px;color:#fff;font-size:13.5px;line-height:26px}
.stat{width:229px}
.stat .shape{height:125px;background:var(--teal);border-radius:70px 0 125px 70px/62px 0 125px 62px;display:flex;align-items:center;justify-content:center;gap:14px;color:var(--navy);font-family:"Ubuntu",sans-serif;font-weight:700;font-size:26px}
.stat p{text-align:center;font-size:16px;line-height:29px;color:#666;margin-top:22px;padding:0 6px}
.testis{top:2549px;left:0;width:1200px;height:493px;background:var(--grey)}
.tcard{width:440px}
.avatar{width:78px;height:78px;border-radius:50%;background:linear-gradient(135deg,#d49a74,#7a4a35)}
.tcard .name{position:absolute;left:100px;top:15px;font-size:16px;font-weight:700;color:#222}
.tcard .role{position:absolute;left:100px;top:44px;font-size:14px;color:#222}
.stars{position:absolute;left:100px;top:64px;color:#f3b700;font-size:12px;letter-spacing:1px}
.quote{position:absolute;right:0;top:5px;font-size:40px;font-weight:700;color:#222;font-family:Georgia,serif}
.tcard p{position:absolute;top:108px;left:2px;width:440px;font-size:13px;line-height:25px;color:#333}
.arrow{width:24px;height:24px;border-radius:50%;display:flex;align-items:center;justify-content:center}
.post{width:313px;height:373px;background:#fff;box-shadow:0 2px 10px rgba(0,0,0,.1)}
.post .pic{height:210px}
.post .tag{padding:22px 14px 0;color:var(--orange);font-size:15px;font-weight:700}
.post h3{padding:4px 14px 0;font-weight:400;font-size:18px;line-height:26px;color:#222}
.post .meta{padding:14px 16px;font-size:12.5px;color:#777;display:flex;gap:28px}
.footer{top:3790px;left:0;width:1200px;height:475px;background:var(--navy);color:#fff}
.footer .brand{color:#fff}
.footer .brand b{font-size:64px}
.footer .brand small{color:#fff;font-size:20px;letter-spacing:16px}
.sub{left:558px;top:58px;width:531px;height:55px;background:#fff;border-radius:4px;display:flex;align-items:center}
.sub span{padding-left:20px;font-size:13px;color:#555}
.sub .btn{margin-left:auto;height:55px;width:106px;border-radius:0 4px 4px 0}
.col h4{font-family:"Ubuntu",sans-serif;font-size:22px;font-weight:400;text-decoration:underline;margin-bottom:22px}
.col li{list-style:none;font-size:14.5px;line-height:29px}
.contact li{display:flex;align-items:center;gap:18px;line-height:48px}
.social li{display:flex;align-items:center;gap:12px;line-height:44px}
.sq{width:20px;height:20px;background:#fff;border-radius:3px}
.sq.o{background:var(--orange)}
.copy{left:109px;top:4212px;width:980px;border-top:1px solid #56648a;text-align:center;padding-top:12px;font-size:13.5px;color:#fff}
</style>
</head>
<body>
<div class="page">
  <div class="abs topbar">
    <span>🕒&nbsp; Hours: Mon - Fri 9.am -7 pm</span>
    <span><b>24/7 Help</b> &nbsp;+1 888 888 8888</span>
    <span class="lang">Eng ▾</span>
  </div>
  <header class="abs nav">
    <div class="brand"><b>Calder Health</b><small>SERVICES</small></div>
    <nav class="menu"><span class="on">Home</span><span>About Us</span><span>Services</span><span>Insurance</span><span>Testimonials</span></nav>
    <svg class="search" width="26" height="26" viewBox="0 0 24 24" fill="none" stroke="#222" stroke-width="2"><circle cx="10" cy="10" r="7"/><path d="M15 15l6 6"/></svg>
    <span class="btn" style="width:112px;height:44px">Contact</span>
  </header>

  <section class="abs hero">
    <div class="abs kicker">Calder Health Services</div>
    <h1 class="abs">Supporting <span class="accent">Mental Wellness,</span><br>One Step at a Time</h1>
    <p class="abs">We provide compassionate, confidential mental health services to individuals and families across Washington DC. Whether you're seeking therapy, psychiatry, or support during a difficult time, we're here to walk with you—every step of the way.</p>
    <span class="abs btn" style="left:111px;top:426px;width:212px;height:44px">Make An Appointment</span>
    <div class="abs ph" role="img" aria-label="Woman smiling with eyes closed" style="left:781px;top:13px;width:143px;height:224px;border-radius:72px 72px 0 0;background:linear-gradient(#e6d5c4,#b8a08c)"></div>
    <div class="abs ph" role="img" aria-label="Group of young people in a support circle" style="left:566px;top:240px;width:245px;height:121px;border-radius:60px 0 0 60px"></div>
    <div class="abs ph" role="img" aria-label="Counselor talking with a client on a sofa" style="left:890px;top:233px;width:249px;height:123px;border-radius:0 62px 62px 0;background:linear-gradient(135deg,#d6d9cf,#7e8b6a)"></div>
    <div class="abs ph" role="img" aria-label="Clinician holding a patient's hands" style="left:758px;top:356px;width:147px;height:233px;border-radius:0 0 74px 74px;background:linear-gradient(#9fd6d4,#d7a98a)"></div>
  </section>

  <div class="abs section-head" style="top:808px">
    <div class="eyebrow">HOW WE HELP YOU</div>
    <h2>Services <span>We Offer</span></h2>
    <div class="rule"></div>
  </div>

  <div class="abs card" style="left:111px;top:962px">
    <div class="pic ph" role="img" aria-label="Psychiatrist listening to a client"></div>
    <div class="title">Psychiatric<br><span>Consultations</span><span class="num">01</span></div>
    <p>Lorem ipsum dolor sit amet, consectetur adipiscing elit, sed do eiusmod tempor incididunt ut labore et dolore magna aliqua.</p>
    <div class="more">Click Here <svg width="14" height="14"><circle cx="7" cy="7" r="7" fill="#0d2147"/><path d="M4 7h6M7 4l3 3-3 3" stroke="#fff" fill="none"/></svg></div>
  </div>
  <div class="abs card active" style="left:357px;top:962px">
    <div class="pic ph" role="img" aria-label="Counseling session in a bright office" style="background:linear-gradient(135deg,#e0ddd6,#8a7f70)"></div>
    <div class="title">Substance<br><span>Abuse/Addiction</span><span class="num" style="color:#c4e6e7">02</span></div>
    <p>Lorem ipsum dolor sit amet, consectetur adipiscing elit, sed do eiusmod tempor incididunt ut labore et dolore magna aliqua.</p>
    <div class="more" style="border-color:#c4e6e7">Click Here <svg width="14" height="14"><circle cx="7" cy="7" r="7" fill="#fff"/><path d="M4 7h6M7 4l3 3-3 3" stroke="#8dcfd2" fill="none"/></svg></div>
  </div>
  <div class="abs card" style="left:604px;top:962px">
    <div class="pic ph" role="img" aria-label="Family in a counseling session" style="background:linear-gradient(135deg,#b9b3a8,#4f4a44)"></div>
    <div class="title">Family Counseling<br><span>&amp;Therapy</span><span class="num">03</span></div>
    <p>Lorem ipsum dolor sit amet, consectetur adipiscing elit, sed do eiusmod tempor incididunt ut labore et dolore magna aliqua.</p>
    <div class="more">Click Here <svg width="14" height="14"><circle cx="7" cy="7" r="7" fill="#0d2147"/><path d="M4 7h6M7 4l3 3-3 3" stroke="#fff" fill="none"/></svg></div>
  </div>
  <div class="abs card" style="left:851px;top:962px">
    <div class="pic ph" role="img" aria-label="Caregiver comforting an older man" style="background:linear-gradient(135deg,#9fb3c3,#7a6a5e)"></div>
    <div class="title">Behavioral<br><span>Health</span><span class="num">04</span></div>
    <p>Lorem ipsum dolor sit amet, consectetur adipiscing elit, sed do eiusmod tempor incididunt ut labore et dolore magna aliqua.</p>
    <div class="more">Click Here <svg width="14" height="14"><circle cx="7" cy="7" r="7" fill="#0d2147"/><path d="M4 7h6M7 4l3 3-3 3" stroke="#fff" fill="none"/></svg></div>
  </div>

  <section class="abs about">
    <div class="abs eyebrow">WHO WE ARE</div>
    <h2 class="abs">About <span class="accent" style="font-weight:500">Us</span></h2>
    <div class="abs rule"></div>
    <p class="abs" style="top:164px">At Calder Health Service, we believe that mental health is essential to overall well-being—and everyone deserves access to compassionate, expert care.</p>
    <p class="abs" style="top:250px">Based in the heart of Washington DC, we provide comprehensive mental health services for individuals, couples, and families. Whether you're navigating anxiety, depression, trauma, or life's many transitions, our licensed team of therapists, psychiatrists, and counselors are here to walk beside you with empathy and professionalism.</p>
    <span class="abs btn" style="left:640px;top:427px;width:114px;height:43px">Read More</span>
  </section>
  <div class="abs about-img" role="img" aria-label="Young people talking together in a group circle"></div>

  <div class="abs section-head" style="top:2102px">
    <div class="eyebrow">OUR IMPACT</div>
    <h2>Proven Outcomes, <span>Trusted Care</span></h2>
    <div class="rule"></div>
  </div>
  <div class="abs stat" style="left:109px;top:2259px"><div class="shape"><svg width="36" height="32" viewBox="0 0 24 24" fill="#0d2147"><circle cx="8" cy="6" r="3"/><path d="M3 20v-6a5 5 0 0 1 10 0v6z"/><path d="M17 3l1 2 2 1-2 1-1 2-1-2-2-1 2-1z"/></svg>30+</div><p>years of combined clinical experience</p></div>
  <div class="abs stat" style="left:358px;top:2259px"><div class="shape" style="padding-bottom:10px"><svg width="38" height="32" viewBox="0 0 24 24" fill="#0d2147"><circle cx="6" cy="5" r="2.5"/><circle cx="17" cy="5" r="2.5"/><path d="M2 20v-8h8v8zM13 20v-8h8v8z"/></svg>60,000+</div><p>Visit through 28 programs per year</p></div>
  <div class="abs stat" style="left:608px;top:2259px"><div class="shape"><svg width="34" height="34" viewBox="0 0 24 24" fill="#0d2147"><path d="M12 2l3 7h7l-6 4.5 2.5 7.5-6.5-4.5-6.5 4.5 2.5-7.5L2 9h7z"/></svg>4.9</div><p>average rating from verified clients</p></div>
  <div class="abs stat" style="left:858px;top:2259px"><div class="shape"><svg width="40" height="32" viewBox="0 0 24 24" fill="none" stroke="#0d2147" stroke-width="2.4"><path d="M2 10l5-4 5 4 5-4 5 4-8 8h-4z"/></svg>74+</div><p>Collaborative Partners for Service Coordination and Advocacy</p></div>

  <section class="abs testis">
    <div class="abs section-head" style="top:40px">
      <div class="eyebrow">TESTIMONIALS</div>
      <h2>What Our <span>Clients Say</span></h2>
      <div class="rule"></div>
    </div>
    <div class="abs tcard" style="left:117px;top:209px">
      <div class="avatar" role="img" aria-label="Portrait of client Nora P"></div>
      <div class="name">Nora P</div><div class="role">School Counselor, Maple Middle School</div><div class="stars">★★★★★</div>
      <div class="quote">❞</div>
      <p>"For the first time in a long time, I feel like I'm in control of my life. My therapist helped me work through years of anxiety with patience and compassion."</p>
    </div>
    <div class="abs" style="left:597px;top:222px;height:200px;border-left:2px dashed #999"></div>
    <div class="abs tcard" style="left:650px;top:209px">
      <div class="avatar" role="img" aria-label="Portrait of client Leah M." style="background:linear-gradient(135deg,#e8a07c,#9c5a3e)"></div>
      <div class="name">Leah M.</div><div class="role">Working Professional</div><div class="stars">★★★★★</div>
      <div class="quote">❞</div>
      <p style="top:100px;font-size:12.5px">"Being able to access care virtually was a game changer. My sessions fit into my schedule, and I always feel heard and understood—even through a screen."</p>
    </div>
    <div class="abs arrow" style="left:36px;top:325px;background:var(--orange)"><svg width="12" height="12"><path d="M10 6H2M6 2L2 6l4 4" stroke="#fff" stroke-width="2" fill="none"/></svg></div>
    <div class="abs arrow" style="left:1124px;top:325px;background:#999"><svg width="12" height="12"><path d="M2 6h8M6 2l4 4-4 4" stroke="#fff" stroke-width="2" fill="none"/></svg></div>
  </section>

  <div class="abs section-head" style="top:3130px">
    <div class="eyebrow">BLOG</div>
    <h2 style="margin-top:4px">Latest <span>News &amp; Updates</span></h2>
    <div class="rule" style="margin-top:8px"></div>
  </div>
  <div class="abs post" style="left:113px;top:3244px">
    <div class="pic ph" role="img" aria-label="Two women reviewing notes together" style="background:linear-gradient(135deg,#e4e4e2,#8c7a6c)"></div>
    <div class="tag">News</div><h3>What Therapy Really Feels Like: A First-Time Client's Guide</h3>
    <div class="meta"><span>▦ June 12,2024</span><span>▭ 4 Comments</span></div>
  </div>
  <div class="abs post" style="left:444px;top:3244px">
    <div class="pic ph" role="img" aria-label="Therapist taking notes with a client" style="background:linear-gradient(135deg,#eeeeec,#5c5c5c)"></div>
    <div class="tag">News</div><h3>Navigating Anxiety in a Busy City: Tips for DC Professionals</h3>
    <div class="meta"><span>▦ June 09,2024</span><span>▭ 4 Comments</span></div>
  </div>
  <div class="abs post" style="left:773px;top:3244px">
    <div class="pic ph" role="img" aria-label="Smiling woman in a counseling session" style="background:linear-gradient(135deg,#c9d3d8,#7b6656)"></div>
    <div class="tag">News</div><h3>The Power of Routine: Mental Health Habits That Actually Work</h3>
    <div class="meta"><span>▦ June 07,2024</span><span>▭ 4 Comments</span></div>
  </div>
  <span class="abs btn" style="left:543px;top:3645px;width:114px;height:43px">Read More</span>

  <footer class="abs footer">
    <div class="abs brand" style="left:119px;top:33px"><b>Calder Health</b><small>SERVICES</small></div>
    <div class="abs sub"><span>Enter Email Address</span><span class="btn">Subscribe</span></div>
    <div class="abs col" style="left:113px;top:187px"><h4>Quick Links</h4><ul><li>Start</li><li>About Me</li><li>Services</li><li>Blog</li><li>Contact</li><li>FAQ's</li></ul></div>
    <div class="abs col" style="left:366px;top:187px"><h4>Other Links</h4><ul><li>Privacy Policy</li><li>Terms &amp; Conditions</li><li>Disclaimer</li><li>Support</li><li>Help</li></ul></div>
    <div class="abs col contact" style="left:636px;top:187px"><h4 style="margin-bottom:8px">Contact Info</h4><ul>
      <li><svg width="22" height="22" viewBox="0 0 24 24"><rect width="24" height="24" rx="4" fill="#fff"/><path d="M12 5a5 5 0 0 0-5 5c0 4 5 9 5 9s5-5 5-9a5 5 0 0 0-5-5z" fill="#0d2147"/></svg>Lorem Ipsum ,USA -437916</li>
      <li><svg width="22" height="22" viewBox="0 0 24 24"><rect width="24" height="24" rx="4" fill="#fff"/><path d="M7 5l3 3-2 2a9 9 0 0 0 6 6l2-2 3 3-2 3C10 20 4 14 4 7z" fill="#0d2147"/></svg>+1 888 888 888</li>
      <li><svg width="22" height="22" viewBox="0 0 24 24"><rect width="24" height="24" rx="4" fill="#fff"/><path d="M5 8h14v9H5zM5 8l7 5 7-5" stroke="#0d2147" stroke-width="1.6" fill="none"/></svg>info@calderhealthservices.com</li></ul></div>
    <div class="abs col social" style="left:973px;top:187px"><h4 style="margin-bottom:4px">Follow US</h4><ul>
      <li><span class="sq o"></span><span style="text-decoration:underline">Friendbook</span></li>
      <li><span class="sq"></span>Snapgram</li>
      <li><span class="sq"></span>Workline</li></ul></div>
  </footer>
  <div class="abs copy">© 2025 &nbsp;Calder Health Services. All rights reserved.</div>
</div>
</body>
</html>
```